Web Design Project

Psychotherapy and Counselling Practice needs a landing page web design.

My business "Larkfield Advisory" specialises in the treatment of Anxiety and Depression with a holistic approach, endeavouring to unlock the key that holds us to ransom in a life that is imbalanced, frustrating, and ultimately of our own making due to our own perceptions and behaviours.

There is much that impacts us which we cannot change, but we are always in control of how we think, and how we frame our experiences.....learning to challenge those thoughts and behaviours that are destructive and disempowering opens up a world of joyful possibility. Life is about making choices, learn to make wiser and healthier choices.......

Larkfield Advisory has a client base of individual clients but will seek to expand to offer services to the Corporate world by offering an adjunct to employers for established "Wellness Programs".

Larkfield Advisory is a highly professional, ethically bound business, with the needs of the client at the forefront of all we do.

Larkfield Advisory wishes to avoid the usual "jargon driven" psychobabble offered on many counselling web pages. It aims to be stylishly presented, clean in look and with as few "words" as possible and a largely white background (faster loading and more powerful impact of what is stated), those words contained in the webpage should be meaningful, persuasive and have an impact simply at glance. Larkfield does not want , or expect, those prospective clients in need of support , to be reading through volumes of industry driven cliches.

At this point Larkfield is just looking for a high quality landing page. However in time this will likely expand to include other sections such as case studies, video content etc.

Target Market(s)

Those in need of emotional support, suffering mental health issues, and those simply wanting to become self aware supported by a mindful therapist.

Industry/Entity Type

Industry

Requirements
Must have
• The design must incorporate the Larkfield logo and colour schemes found on the attached files.

```html
<!DOCTYPE html>
<html lang="en">
<head>
<meta charset="utf-8">
<title>Larkfield Advisory — Your wellness starts today</title>
<link rel="stylesheet" href="https://fonts.googleapis.com/css2?family=Open+Sans:wght@300;400;600&display=swap">
<style>
  :root {
    --green: #7fad1c;
    --green-dark: #6b9614;
    --grey-band: #6d6d6d;
    --grey-text: #444444;
    --grey-soft: #5f5f5f;
    --grey-circle: #6b6b6b;
    --white: #ffffff;
    --ink: #222222;
    --photo-dark: #1c1c1c;
    --photo-light: #9a9a9a;
  }
  * { margin: 0; padding: 0; box-sizing: border-box; }
  html, body { width: 1200px; height: 1200px; overflow: hidden; background: var(--white); }
  body { font-family: "Open Sans", Arial, sans-serif; color: var(--grey-text); }
  .page { position: relative; width: 1200px; height: 1200px; overflow: hidden; }
  .abs { position: absolute; }

  .backdrop { position: absolute; left: 0; top: 0; width: 1200px; height: 1200px; }

  /* Header */
  .brand { left: 215px; top: 112px; font-size: 50px; font-weight: 300; color: var(--green); letter-spacing: 1px; line-height: 1; }
  .account-links { left: 560px; top: 25px; font-size: 11px; font-weight: 600; color: var(--ink); }
  .account-links span { margin: 0 6px; font-weight: 400; }
  .phone { left: 848px; top: 20px; font-size: 22px; font-weight: 400; color: var(--grey-soft); letter-spacing: 1px; white-space: nowrap; }
  .phone b { color: var(--green); font-weight: 600; margin-right: 10px; }

  .main-nav { left: 519px; top: 68px; width: 510px; height: 47px; background: linear-gradient(var(--green), var(--green-dark)); display: flex; align-items: center; justify-content: space-around; padding: 0 12px; }
  .main-nav a { color: var(--white); text-decoration: none; font-size: 20px; font-weight: 600; text-transform: uppercase; }
  .main-nav .sep { width: 1px; height: 14px; background: rgba(255,255,255,0.6); }

  .headline { left: 557px; top: 128px; font-size: 36px; font-weight: 400; color: var(--green); white-space: nowrap; line-height: 1.2; }
  .tagline { left: 557px; top: 180px; font-size: 22px; font-weight: 400; color: var(--grey-text); line-height: 30px; white-space: nowrap; }

  /* Hero band */
  .social-hero { left: 387px; top: 323px; display: flex; gap: 4px; }
  .social-dot { width: 26px; height: 26px; border-radius: 50%; background: var(--white); border: 2px solid #3a3a3a; }
  .hero-text { left: 196px; top: 370px; font-size: 25px; font-weight: 300; color: var(--white); line-height: 33px; white-space: nowrap; }
  .search { left: 336px; top: 519px; width: 199px; height: 22px; border-radius: 11px; background: linear-gradient(#f4f4f4, #d8d8d8); border: 1px solid #9c9c9c; font-size: 11px; color: #555; padding: 3px 0 0 9px; }
  .search svg { position: absolute; right: 8px; top: 4px; }
  .hero-photo { left: 628px; top: 298px; width: 402px; height: 262px; border: 3px solid #2d2d2d; background: linear-gradient(100deg, var(--photo-dark) 0%, #2a2a2a 35%, var(--photo-light) 60%, #5a5a5a 100%); }

  /* Statement */
  .statement { left: 196px; top: 643px; font-size: 25px; line-height: 38px; font-weight: 400; white-space: nowrap; }
  .statement .lead { color: var(--green); }
  .statement .follow { color: var(--grey-text); }
  .btn { background: var(--green); color: var(--white); font-size: 14px; font-weight: 600; text-transform: uppercase; text-align: center; line-height: 34px; height: 34px; }
  .btn-consult-top { left: 865px; top: 682px; width: 144px; }

  /* Feature columns */
  .feature { top: 764px; width: 300px; text-align: center; }
  .feature .badge { width: 124px; height: 124px; border-radius: 50%; background: var(--grey-circle); margin: 0 auto; display: flex; align-items: center; justify-content: center; }
  .feature h2 { margin-top: 20px; font-size: 25px; font-weight: 400; color: var(--green); }
  .feature p { margin: 14px auto 0; width: 250px; font-size: 12px; line-height: 20px; color: var(--grey-text); }
  .feature-talk p { width: 262px; }
  .feature .btn { position: absolute; top: 280px; left: 50%; transform: translateX(-50%); width: 145px; }
  .feature-who { left: 167px; }
  .feature-growing { left: 434px; }
  .feature-talk { left: 710px; }

  .title-bar { width: 4px; height: 27px; background: var(--green); top: 898px; }
  .divider { top: 895px; width: 0; height: 180px; border-left: 1px dotted #b5b5b5; }

  /* Footer */
  .footer-nav { left: 196px; top: 1120px; font-size: 14px; font-weight: 600; color: var(--grey-text); text-transform: uppercase; display: flex; gap: 8px; }
  .footer-nav .sep { color: var(--grey-soft); font-weight: 400; }
  .copyright { left: 196px; top: 1148px; font-size: 12px; color: var(--grey-soft); }
  .social-footer { left: 714px; top: 1137px; display: flex; gap: 4px; }
  .social-footer .social-dot { background: var(--ink); border: none; }
  .footer-brand { left: 866px; top: 1133px; font-size: 27px; font-weight: 300; color: var(--green); letter-spacing: 1px; }
</style>
</head>
<body>
<div class="page">

  <svg class="backdrop" viewBox="0 0 1200 1200" aria-hidden="true">
    <path d="M0 280 H170 Q420 262 800 280 H1200 V563 H1030 Q900 620 620 622 Q400 620 250 563 H0 Z" fill="var(--grey-band)"/>
    <path d="M170 268 Q420 250 820 282 Q420 264 170 283 Z" fill="var(--green)"/>
    <path d="M250 563 Q420 612 620 622 Q880 618 1030 563 Q880 632 620 627 Q420 626 250 563 Z" fill="var(--green)"/>
    <ellipse cx="600" cy="1080" rx="440" ry="4" fill="#d0d0d0" opacity="0.6"/>
  </svg>

  <!-- Header -->
  <div class="abs brand">LARKFIELD</div>
  <div class="abs account-links">Login<span>|</span>Register</div>
  <div class="abs phone"><b>M</b>0400 218 765</div>

  <nav class="abs main-nav">
    <a href="#">Home</a><span class="sep"></span>
    <a href="#">About</a><span class="sep"></span>
    <a href="#">Services</a><span class="sep"></span>
    <a href="#">Contact</a><span class="sep"></span>
    <a href="#">FAQs</a>
  </nav>

  <h1 class="abs headline">Your wellness starts today</h1>
  <p class="abs tagline">specialises in the treatment of Anxiety and<br>Depression with a holistic approach</p>

  <!-- Hero -->
  <div class="abs social-hero" aria-label="Social links">
    <span class="social-dot"></span><span class="social-dot"></span><span class="social-dot"></span><span class="social-dot"></span>
  </div>
  <p class="abs hero-text">Dr. MAE HOLLIS commitment<br>to provide quality healthcare<br>for your whole family drives<br>everything we do.</p>
  <div class="abs search">Search
    <svg width="12" height="12" viewBox="0 0 12 12"><circle cx="5" cy="5" r="3.5" fill="none" stroke="#555" stroke-width="1.5"/><line x1="7.5" y1="7.5" x2="11" y2="11" stroke="#555" stroke-width="1.8"/></svg>
  </div>
  <div class="abs hero-photo" role="img" aria-label="Black and white photo of a person sitting on the floor against a wall, head in hands, backlit by a window"></div>

  <!-- Statement -->
  <p class="abs statement"><span class="lead">Larkfield Advisory is a highly professional, ethically bound business,</span><br><span class="follow">with the needs of the client at the forefront of all we do.</span></p>
  <div class="abs btn btn-consult-top">Consult Us</div>

  <!-- Features -->
  <section class="abs feature feature-who">
    <div class="badge">
      <svg width="70" height="70" viewBox="0 0 70 70" fill="none" stroke="var(--green)" stroke-width="4">
        <circle cx="35" cy="26" r="16"/><circle cx="25" cy="43" r="16"/><circle cx="45" cy="43" r="16"/>
      </svg>
    </div>
    <h2>Who We Are</h2>
    <p>Lorem ipsum dolor sit amet, consectetuer adipiscing elit, sed diam nonummy nibh euismod tincidunt ut laoreet dolore magna aliquam erat volutpat.</p>
    <div class="btn">Get to know us</div>
  </section>

  <section class="abs feature feature-growing">
    <div class="badge">
      <svg width="70" height="70" viewBox="0 0 70 70" stroke="var(--green)" stroke-width="3" fill="var(--green)">
        <line x1="35" y1="35" x2="35" y2="9"/><line x1="35" y1="35" x2="35" y2="61"/>
        <line x1="35" y1="35" x2="12" y2="22"/><line x1="35" y1="35" x2="58" y2="22"/>
        <line x1="35" y1="35" x2="12" y2="48"/><line x1="35" y1="35" x2="58" y2="48"/>
        <circle cx="35" cy="9" r="4.5"/><circle cx="35" cy="61" r="4.5"/>
        <circle cx="12" cy="22" r="4.5"/><circle cx="58" cy="22" r="4.5"/>
        <circle cx="12" cy="48" r="4.5"/><circle cx="58" cy="48" r="4.5"/>
      </svg>
    </div>
    <h2>We’re Growing!</h2>
    <p>Ut wisi enim ad minim veniam, quis nostrud exerci tation ullamcorper suscipit lobortis nisl ut aliquip ex ea commodo consequat.</p>
    <div class="btn">How we helps</div>
  </section>

  <section class="abs feature feature-talk">
    <div class="badge">
      <svg width="70" height="70" viewBox="0 0 70 70" fill="none" stroke="var(--green)" stroke-width="4">
        <circle cx="35" cy="35" r="28"/><circle cx="35" cy="35" r="17"/><circle cx="35" cy="35" r="7" fill="var(--green)"/>
      </svg>
    </div>
    <h2>Let’s Talk about You</h2>
    <p>Duis autem vel eum iriure dolor in hendrerit in vulputate velit esse molestie consequat, vel illum dolore eu feugiat nulla facilisis at vero eros et accumsan et iusto odio.</p>
    <div class="btn">Consult Us</div>
  </section>

  <span class="abs title-bar" style="left:447px"></span>
  <span class="abs title-bar" style="left:720px"></span>
  <span class="abs divider" style="left:451px"></span>
  <span class="abs divider" style="left:724px"></span>

  <!-- Footer -->
  <nav class="abs footer-nav">
    <span>Home</span><span class="sep">|</span><span>About</span><span class="sep">|</span><span>Services</span><span class="sep">|</span><span>Contact</span><span class="sep">|</span><span>FAQs</span>
  </nav>
  <p class="abs copyright">Copyright © 2013 Larkfield</p>
  <div class="abs social-footer" aria-label="Social links">
    <span class="social-dot"></span><span class="social-dot"></span><span class="social-dot"></span><span class="social-dot"></span>
  </div>
  <div class="abs footer-brand">LARKFIELD</div>

</div>
</body>
</html>
```